Design a cool print brochure for an NGO / Give your work a global impact!!

Hi,
I provide a full design brief (below, please scroll) and a mood board (attached) to help you visualize inside my head.. ;-)
I am also available to help and have worked many years in advertising; we will understand each other.
Objective:
To design an A4 folded in two presentation brochure for a non-profit consulting agency called Verdomo.
Verdomo works in sustainability and international development = working with NGO’s, governments and private sector on global issues such as global warming, education for all etc.
Strategy:
This document is a first step in developing a communication strategy. It will be distributed during a major international event called the Brightwater Aid Forum.
Objective:
The double objective of the brochure is:
a) to inform the recipient of what Verdomo is, in the shortest time possible.
b) to showcase relevant projects to demonstrate Verdomo experience and expertise.
Target:
Main target:
Existing Verdomo contacts, such as members of development organizations, NGOs, private sector foundations (CSR), regional networks and other development actors.
NB: the main target already has a certain awareness of Verdomo: we will try to minimize text to maximize visual impact and readability.
Secondary target:
Verdomo will also distribute the brochure to new prospects of interest during the Brightwater Forum.
Timing:
We will need to finalize the design and have the files by June 1st to allow time for print before the event.
Content:
The document should be concise, highly readable (no clutter) and include:
1. text (that we will provide)
and
2. visual elements such as images, shapes and info-graphics (that is you).
NB: Verdomo does not have its own image bank; photos will be provided by you.
Format:
A4 folded in half - 4pp A5 - PORTRAIT FORMAT) with an impactful visual in the front, logo, title and headline (please see examples in the mood board attached).
Design elements:
Verdomo does not have yet a visual identity (please see: http://verdomo.org) so there is room for creativity and no graphic chart to follow.
The sector of consulting in international development is rather conservative but our intention is to be disruptive and create a “Wow” effect. We count on you for that!
Therefore, the design should be “structured”, “organized”, “uncluttered” but also “modern”, “impactful”, “highly visual” (think infographic or mind map to describe our services and projects).
Please, take the time to see the attached presentation: I give you guidelines and examples of what we want and what we like.
We are looking forward to seeing your work and I am available for comments, questions and support.
Thank you.
RK
Target Market(s)
The full brief is in the project description: please, scroll through it.
The target market is : our existing clients base, working in sustainable development (read: NGO and Allied Assembly people)
Industry/Entity Type
Ngo
Font styles to use
Requirements
Must have
- - Design and color elements: please, no black and white. Our company website is in black and white and without graphics; we want the brochure to break away from that and start creating our brand identity; so please, show us colors and desing elements (shapes, backgrounds, etc).
- You have a chance to showcase your talent in terms of visual identity: what lines, forms, layout and colors can you come up with and apply throughout the brochure and serve as the visual identity of Verdomo?
- The structure of the document should be:
- - Front cover: design elements + impacful photo (see mood board example attached) +our logo + this headline: "Collective action for sustainable development and impact"
- - Inside front: a graphic representation of "Our Services": such as core activity in the center circle and satellite circles for the services we offer.
- - Inside back:
- 1. Icons and text boxes for "Our projects"
- 2. A world map of the countries where we have worked. Full list of countries is here:
- http://verdomo.org/experience-1
- - Back cover: our contact + logos of partners.
- Our partners are listed here:
- Please use their original logos (ie, in color).
- The design we will select will serve as a basis for a graphic chart...so more work to come...word to the wise ;)
- Please check out our website verdomo.org to see what we do etc.
Nice to have
- Icons to reflect our services: what icons can you come up with to describe "training services", "building networks" or "program management"?
- I give examples in the mood board.
Should not have
- We are open to creativity and want to generate a "Wow" effect.
- Just note that the sector is rather conservative so flashy colors and cartoon like characters should be avoided. Think "earth, global change, Allied Assembly, climate" without going too green (it's overdone). ;-)
- Make us stand out in the NGO world
- Now you.

```html
<!DOCTYPE html>
<html lang="en">
<head>
<meta charset="utf-8">
<title>Verdomo – brochure inner spread</title>
<link href="https://fonts.googleapis.com/css2?family=Montserrat:wght@400;600;700&family=Noto+Serif:wght@400&display=swap" rel="stylesheet">
<style>
  :root{
    --stage:#d4d4d4;
    --paper-light:#eef1cf;
    --paper-dark:#d6ddb0;
    --olive:#9c9a5a;
    --olive-deep:#85844a;
    --orange:#f07c3c;
    --amber:#e0a52a;
    --lime:#b9d43a;
    --green:#7fbf3f;
    --teal:#1fa88f;
    --teal-light:#7fcbc6;
    --aqua:#2bb7a6;
    --ink:#5b5a40;
    --white:#ffffff;
  }
  *{box-sizing:border-box;margin:0;padding:0}
  html,body{width:1200px;height:1200px;overflow:hidden;background:var(--stage)}
  .spread{
    position:absolute;left:20px;top:190px;width:1160px;height:820px;overflow:hidden;
    background:radial-gradient(ellipse at 60% 70%, var(--paper-light) 0%, #e4e9c0 55%, var(--paper-dark) 100%);
  }
  .decor{position:absolute;left:0;top:0}
  .world-map{
    position:absolute;left:389px;top:40px;width:771px;height:420px;
    border-radius:45% 40% 35% 45%;
    background:radial-gradient(ellipse at 22% 40%, rgba(127,191,63,.55) 0%, rgba(127,191,63,0) 35%),
               radial-gradient(ellipse at 55% 20%, rgba(43,183,166,.45) 0%, rgba(43,183,166,0) 22%),
               radial-gradient(ellipse at 58% 55%, rgba(240,124,60,.35) 0%, rgba(180,165,110,.35) 25%, rgba(180,165,110,0) 40%),
               radial-gradient(ellipse at 85% 45%, rgba(200,170,90,.45) 0%, rgba(200,170,90,0) 40%);
  }
  .heading{position:absolute;font-family:"Noto Serif",serif;color:var(--white);line-height:.95}
  .heading .big{display:block;font-size:48px}
  .heading .small{display:block;font-size:30px}
  .heading.glance{left:56px;top:26px}
  .heading.presence{right:46px;top:28px;text-align:right}
  .heading.projects{right:46px;top:715px;text-align:right}

  .service{position:absolute;width:104px;height:104px;border-radius:50%;display:flex;align-items:center;justify-content:center}
  .service svg{width:58px;height:58px}
  .service.research{left:237px;top:264px;background:var(--orange)}
  .service.facilitation{left:70px;top:368px;background:var(--lime)}
  .service.training{left:382px;top:368px;background:var(--orange)}
  .service.methodologies{left:70px;top:530px;background:var(--green)}
  .service.evaluation{left:382px;top:530px;background:var(--teal-light)}
  .service.coalition{left:237px;top:636px;background:var(--teal)}

  .core{
    position:absolute;left:179px;top:384px;width:228px;height:228px;border-radius:50%;
    background:radial-gradient(circle at 40% 35%, #e9e32c 0%, #d8dc2a 35%, #f0a23a 70%, #5fbf63 100%);
    display:flex;align-items:center;justify-content:center;text-align:center;
    font-family:Montserrat,sans-serif;font-weight:600;font-size:12.5px;line-height:1.3;color:#5b4a1a;text-transform:uppercase;padding:0 40px;
  }
  .label{position:absolute;font-family:Montserrat,sans-serif;font-weight:600;font-size:9.6px;line-height:1.3;color:var(--ink);text-transform:uppercase}
  .label.research{left:200px;top:232px;width:180px;text-align:center}
  .label.facilitation{left:51px;top:332px;width:180px}
  .label.training{left:355px;top:332px;width:175px;text-align:right}
  .label.methodologies{left:51px;top:664px;width:180px}
  .label.evaluation{left:355px;top:664px;width:175px;text-align:right}
  .label.coalition{left:190px;top:760px;width:200px;text-align:center}

  .project-num{position:absolute;width:80px;height:80px;border-radius:50%;display:flex;align-items:center;justify-content:center;font-family:"Noto Serif",serif;font-size:44px;color:var(--white)}
  .project-num.one{left:803px;top:700px;background:var(--teal)}
  .project-num.two{left:897px;top:586px;background:var(--aqua)}
  .project-num.three{left:1043px;top:543px;background:var(--teal-light)}
  .project-text{position:absolute;font-family:Montserrat,sans-serif;font-size:11px;line-height:1.4;color:var(--ink);text-align:right}
  .project-text.one{left:600px;top:635px;width:223px}
  .project-text.two{left:700px;top:527px;width:213px}
  .project-text.three{left:870px;top:484px;width:214px}
</style>
</head>
<body>
<main class="spread">
  <svg class="decor" width="1160" height="820" viewBox="0 0 1160 820" aria-hidden="true">
    <defs>
      <radialGradient id="olive-glow" cx="0.3" cy="0.2" r="0.8">
        <stop offset="0" stop-color="#a6a45e"/><stop offset="1" stop-color="#a6a45e" stop-opacity="0"/>
      </radialGradient>
      <radialGradient id="amber-glow" cx="0.5" cy="0.5" r="0.5">
        <stop offset="0" stop-color="#e8a32a"/><stop offset=".7" stop-color="#e48a2c" stop-opacity=".9"/><stop offset="1" stop-color="#e48a2c" stop-opacity="0"/>
      </radialGradient>
      <radialGradient id="teal-glow" cx="0.5" cy="0.5" r="0.5">
        <stop offset="0" stop-color="#2aa88a"/><stop offset=".75" stop-color="#4fb38f" stop-opacity=".9"/><stop offset="1" stop-color="#4fb38f" stop-opacity="0"/>
      </radialGradient>
    </defs>
    <!-- top-left rings -->
    <circle cx="110" cy="40" r="230" fill="url(#olive-glow)" opacity=".8"/>
    <g fill="none" stroke="#8f8d50" stroke-width="10" opacity=".75">
      <circle cx="140" cy="60" r="150"/><circle cx="140" cy="60" r="185"/><circle cx="140" cy="60" r="215"/>
    </g>
    <!-- top-right presence -->
    <circle cx="1080" cy="80" r="260" fill="url(#amber-glow)" opacity=".85"/>
    <g fill="none" stroke="#f2c45a" stroke-width="8" opacity=".6">
      <circle cx="1080" cy="80" r="170"/><circle cx="1080" cy="80" r="205"/><circle cx="1080" cy="80" r="240"/>
    </g>
    <!-- bottom-right projects -->
    <circle cx="1100" cy="800" r="210" fill="url(#teal-glow)"/>
    <g fill="none" stroke="#1e9c7f" stroke-width="7" opacity=".7">
      <circle cx="1100" cy="820" r="190"/><circle cx="1100" cy="820" r="225"/><circle cx="1100" cy="820" r="260"/>
    </g>
    <!-- service diagram rings -->
    <g fill="none" stroke-width="3" opacity=".7">
      <circle cx="293" cy="498" r="132" stroke="#f08a3c"/>
      <circle cx="293" cy="498" r="148" stroke="#3fae76"/>
      <circle cx="289" cy="316" r="66" stroke="#f4a070" opacity=".6"/>
      <circle cx="434" cy="420" r="66" stroke="#f4a070" opacity=".6"/>
      <circle cx="122" cy="582" r="66" stroke="#9cc86a" opacity=".6"/>
      <circle cx="289" cy="688" r="66" stroke="#6fc2a6" opacity=".6"/>
    </g>
  </svg>

  <div class="world-map" role="img" aria-label="World map highlighting the countries where Verdomo has worked, linked by dotted flight-path lines"></div>

  <h1 class="heading glance"><span class="big">verdomo</span><span class="small">at a glance</span></h1>
  <h2 class="heading presence"><span class="big">our</span><span class="small">presence</span></h2>
  <h2 class="heading projects"><span class="big">our</span><span class="small">projects</span></h2>

  <section class="services">
    <div class="core">Analysis of multi-actor cooperation and the facilitation of processes of change</div>

    <div class="service research"><svg viewBox="0 0 60 60" fill="none" stroke="#fff" stroke-width="2.4" stroke-linecap="round" stroke-linejoin="round"><path d="M8 34l10-10 8 4 8-6 8 6 10 6"/><path d="M18 24l10 14 6-4 6 6"/><path d="M34 10l8-8 0 6M42 2h-6"/><path d="M16 40v6M24 38v8M32 36v10"/></svg></div>
    <div class="service facilitation"><svg viewBox="0 0 60 60" fill="none" stroke="#fff" stroke-width="2.4" stroke-linecap="round" stroke-linejoin="round"><path d="M6 42c8-2 14 2 20 2h12c3 0 3-5 0-5h-9"/><path d="M6 52c10 0 22 4 32-2l14-9c2-2 0-5-3-4l-12 6"/><path d="M32 36V18"/><path d="M32 24c-8 0-10-8-10-12 6 0 10 4 10 12zM32 20c0-8 6-12 12-12 0 8-6 12-12 12z"/></svg></div>
    <div class="service training"><svg viewBox="0 0 60 60" fill="none" stroke="#fff" stroke-width="2.4" stroke-linecap="round"><circle cx="20" cy="18" r="7"/><circle cx="40" cy="18" r="7"/><circle cx="30" cy="40" r="7"/><circle cx="10" cy="46" r="4"/><circle cx="50" cy="46" r="4"/><path d="M25 23l3 10M35 23l-3 10M27 18h6M24 43l-10 2M36 43l10 2"/></svg></div>
    <div class="service methodologies"><svg viewBox="0 0 60 60" fill="none" stroke="#fff" stroke-width="2.4" stroke-linecap="round" stroke-linejoin="round"><rect x="18" y="12" width="24" height="34" rx="2"/><circle cx="30" cy="26" r="6"/><path d="M23 38h14M23 42h10"/><path d="M12 18c-6 8-6 20 2 28M48 18c6 8 6 20-2 28"/></svg></div>
    <div class="service evaluation"><svg viewBox="0 0 60 60" fill="none" stroke="#fff" stroke-width="2.4" stroke-linecap="round" stroke-linejoin="round"><path d="M14 6h24l10 10v38H14z"/><path d="M38 6v10h10"/><circle cx="30" cy="24" r="6"/><path d="M30 18v6h6"/><path d="M20 48V40M26 48V36M32 48V38M38 48V34M18 48h24"/></svg></div>
    <div class="service coalition"><svg viewBox="0 0 60 60" fill="none" stroke="#fff" stroke-width="2.4" stroke-linecap="round" stroke-linejoin="round"><rect x="16" y="16" width="28" height="28" transform="rotate(45 30 30)"/><path d="M8 20l12 0M40 8v12M52 40H40M20 52V40"/></svg></div>

    <p class="label research">Research and analysis<br>of cooperation schemes</p>
    <p class="label facilitation">Facilitation of processes<br>of change</p>
    <p class="label training">Training to improve<br>networked action</p>
    <p class="label methodologies">Methodologies for<br>organizational change<br>and consensus building</p>
    <p class="label evaluation">Evaluation of<br>multi-actor projects<br>and programs</p>
    <p class="label coalition">Coalition building to achieve<br>collective goals</p>
  </section>

  <section class="projects">
    <p class="project-text three">implementation of the Agenda 2030 and the Sustainable Development Goals</p>
    <p class="project-text two">Organizational and technical development of the Northern Commission's Policy Forum on Development</p>
    <p class="project-text one">Networks of CSOs and Local Authorities from the Union and its partner countries, as well as regional institutions</p>
    <div class="project-num one">1</div>
    <div class="project-num two">2</div>
    <div class="project-num three">3</div>
  </section>
</main>
</body>
</html>
```